1 Page for Computer Repair Website

Looking for a 1 page website with a design that compliments the business card and pamphlet that have already been made (attached files). It should look business professional and easy to read. Email and phone number should be somewhere near the top of the website, visible when the page loads. I don't want any forms for people to mess with. No "Contact Us" form or entering in email for newsletter. Customers will just be looking at this site to confirm we are professionals and have our business in order.

Target Market(s)

Home and small business

Industry/Entity Type

Computer Repair

Coding

Coded - Design and coding required

Number of Pages Required

1 page

Font styles to use
Other font styles liked:
• Helvetica variations used in pamphlet and card

Colors
0455a3
cfdeed
85abd2
3276b5
85cae6
ffffff

Requirements
Must have
• Compliment the pamphlet and business card in color choices and font use. Pleasing to the eye and easy to read through categories and text.
Should not have
• Forms. No "enter name and email here" or anything of the sort.

```html
<!DOCTYPE html>
<html lang="en">
<head>
<meta charset="utf-8">
<title>NEXBYTE – Computer Service &amp; Repair</title>
<link rel="stylesheet" href="https://fonts.googleapis.com/css2?family=Arimo:wght@400;700&display=swap">
<style>
:root{
  --navy:#0455a3;
  --mid:#3276b5;
  --soft:#85abd2;
  --sky:#85cae6;
  --pale:#cfdeed;
  --white:#ffffff;
  --ink:#4a4f57;
  --muted:#7d838b;
  --band:#eef1f4;
  --footer:#0a4f95;
}
*{box-sizing:border-box;margin:0;padding:0}
html,body{width:723px;height:1200px;overflow:hidden}
body{font-family:"Arimo",Helvetica,Arial,sans-serif;color:var(--ink);background:var(--white);position:relative}

/* hero */
.hero{position:absolute;left:0;top:0;width:723px;height:330px;
  background:linear-gradient(110deg,#c9d3dd 0%,#9fb0c2 35%,#4d6d91 70%,#20426c 100%)}
.hero-shade{position:absolute;inset:0;background:linear-gradient(180deg,rgba(4,85,163,.25),rgba(4,85,163,.05) 60%,rgba(0,0,0,.15))}
.brand{position:absolute;left:16px;top:14px;display:flex;align-items:center;gap:6px;
  font-weight:700;font-size:18px;color:var(--navy);letter-spacing:.5px}
.brand-dot{width:10px;height:10px;background:var(--navy);border-radius:50%}
.contact{position:absolute;right:18px;top:14px;text-align:right;color:var(--white);font-size:14px;line-height:19px}
.hero-title{position:absolute;left:58px;top:158px;color:var(--white);font-size:26px;font-weight:400;line-height:29px;letter-spacing:.5px}
.hero-dots{position:absolute;left:60px;top:232px;display:flex;gap:6px}
.hero-dots span{width:6px;height:6px;border-radius:50%;background:rgba(255,255,255,.6)}
.hero-dots span:first-child{background:var(--white)}

/* service tiles */
.tiles{position:absolute;left:56px;top:275px;width:610px;height:155px;display:flex}
.tile{flex:1;color:var(--white);text-align:center;padding:18px 22px 0}
.tile-res{background:var(--navy)}
.tile-biz{background:var(--mid)}
.tile-remote{background:var(--soft)}
.tile svg{width:30px;height:26px;display:block;margin:0 auto 8px}
.tile h3{font-size:14px;font-weight:700;line-height:16px;letter-spacing:.3px}
.tile p{font-size:8px;line-height:11px;margin-top:12px;opacity:.9}

/* welcome */
.welcome{position:absolute;left:56px;top:450px;width:610px;height:200px}
.section-title{color:var(--navy);font-size:20px;font-weight:700;letter-spacing:.3px}
.welcome-text{width:320px;margin-top:14px}
.welcome-text p{font-size:8px;line-height:12px;color:var(--muted);margin-bottom:10px}
.btn{display:inline-block;background:var(--navy);color:var(--white);font-size:12px;font-weight:700;padding:9px 13px;border-radius:2px}
.welcome .btn{margin-top:8px}
.video{position:absolute;right:0;top:0;width:260px;height:150px;
  background:linear-gradient(135deg,#e4e9ee 0%,#9aa7b4 45%,#2c3a4a 100%)}

/* services band */
.services{position:absolute;left:0;top:655px;width:723px;height:270px;background:var(--band)}
.services .section-title{position:absolute;left:56px;top:22px}
.arrows{position:absolute;right:58px;top:24px;display:flex;gap:14px}
.arrows svg{width:8px;height:12px}
.service-cards{position:absolute;left:56px;top:62px;width:610px;display:flex;gap:36px}
.card{width:180px}
.card-img{height:98px}
.img-malware{background:linear-gradient(135deg,#1b3d6e,#3d6fa6 55%,#0d2447)}
.img-hardware{background:linear-gradient(135deg,#4a4d52,#8c8f93 50%,#2e3136)}
.img-data{background:linear-gradient(135deg,#0d3b70,#2d7cc4 50%,#0b2a52)}
.card h4{font-size:13px;font-weight:400;color:var(--navy);margin-top:16px;letter-spacing:.2px}
.card p{font-size:8px;line-height:11px;color:var(--muted);margin-top:6px}
.card .more{font-size:8px;color:var(--navy);margin-top:6px;display:block}

/* why choose */
.why-img{position:absolute;left:18px;top:940px;width:285px;height:180px;
  background:linear-gradient(160deg,#f2f4f6 0%,#c7ced6 45%,#6e7f93 100%)}
.why{position:absolute;left:342px;top:950px;width:330px}
.why ul{list-style:none;margin-top:12px}
.why li{font-size:8px;line-height:16px;color:var(--muted);display:flex;align-items:center;gap:7px}
.why li svg{width:7px;height:7px;flex:none}
.why .btn{margin-top:12px}

/* footer */
.footer{position:absolute;left:0;top:1150px;width:723px;height:50px;background:var(--footer);color:var(--white)}
.footer-nav{position:absolute;left:24px;top:14px;display:flex;gap:12px;font-size:7px;letter-spacing:.3px}
.copyright{position:absolute;left:24px;top:30px;font-size:7px;opacity:.8}
.social{position:absolute;right:30px;top:18px;display:flex;gap:6px}
.social span{width:12px;height:12px;border-radius:50%;background:var(--sky)}
.social span:nth-child(2){background:var(--mid)}
.social span:nth-child(3){background:#d9534f}
.social span:nth-child(4){background:var(--soft)}
.social span:nth-child(5){background:var(--pale)}
</style>
</head>
<body>

<header class="hero" role="img" aria-label="Hands typing on a laptop keyboard">
  <div class="hero-shade"></div>
</header>
<div class="brand"><span class="brand-dot"></span>NEXBYTE</div>
<div class="contact">Call us: 555-201-4587<br>Email:sam@nexbyte.com</div>
<h1 class="hero-title">COMPUTER<br>SERVICE &amp; REPAIR</h1>
<div class="hero-dots"><span></span><span></span><span></span></div>

<section class="tiles">
  <div class="tile tile-res">
    <svg viewBox="0 0 30 26"><path d="M15 2 2 13h4v11h7v-7h4v7h7V13h4z" fill="#fff"/></svg>
    <h3>RESIDENTIAL<br>SERVICES</h3>
    <p>Fast home repairs, virus cleanup and upgrades done right at your door.</p>
  </div>
  <div class="tile tile-biz">
    <svg viewBox="0 0 30 26"><path d="M5 4h20v20H5z" fill="#fff"/><g fill="#3276b5"><rect x="8" y="7" width="3" height="3"/><rect x="13.5" y="7" width="3" height="3"/><rect x="19" y="7" width="3" height="3"/><rect x="8" y="13" width="3" height="3"/><rect x="13.5" y="13" width="3" height="3"/><rect x="19" y="13" width="3" height="3"/><rect x="13" y="19" width="4" height="5"/></g></svg>
    <h3>BUSINESS<br>SERVICES</h3>
    <p>Network setup, server care and support plans for small office teams.</p>
  </div>
  <div class="tile tile-remote">
    <svg viewBox="0 0 30 26"><rect x="3" y="3" width="24" height="16" rx="1" fill="none" stroke="#fff" stroke-width="2"/><path d="M11 24h8M15 19v5" stroke="#fff" stroke-width="2"/></svg>
    <h3>REMOTE<br>SUPPORT</h3>
    <p>Secure remote sessions fix most software issues without a site visit.</p>
  </div>
</section>

<section class="welcome">
  <h2 class="section-title">WELCOME TO NEXBYTE</h2>
  <div class="welcome-text">
    <p>Our certified technicians repair desktops, laptops and networks for homes and small businesses. We diagnose problems quickly, explain options in plain language and stand behind every job.</p>
    <p>From slow computers to failed drives, we handle it all with honest pricing and friendly service. Most repairs are finished within two business days.</p>
  </div>
  <span class="btn">Request Quote</span>
  <div class="video" role="img" aria-label="Video still of desktop computer monitors"></div>
</section>

<section class="services">
  <h2 class="section-title">OUR SERVICES</h2>
  <div class="arrows">
    <svg viewBox="0 0 8 12"><path d="M7 1 2 6l5 5" fill="none" stroke="#4a4f57" stroke-width="2"/></svg>
    <svg viewBox="0 0 8 12"><path d="M1 1l5 5-5 5" fill="none" stroke="#4a4f57" stroke-width="2"/></svg>
  </div>
  <div class="service-cards">
    <article class="card">
      <div class="card-img img-malware" role="img" aria-label="Circuit board with glowing security lines"></div>
      <h4>MALWARE/VIRUS REMOVAL</h4>
      <p>Remove viruses, spyware and malware safely and restore your system speed.</p>
      <span class="more">Learn More</span>
    </article>
    <article class="card">
      <div class="card-img img-hardware" role="img" aria-label="Close view of computer hardware components"></div>
      <h4>HARDWARE REPAIR</h4>
      <p>Replace screens, drives, memory and power parts with quality components.</p>
      <span class="more">Learn More</span>
    </article>
    <article class="card">
      <div class="card-img img-data" role="img" aria-label="Digital padlock over blue data streams"></div>
      <h4>DATA MIGRATION</h4>
      <p>Move files, email and settings to your new machine without any loss.</p>
      <span class="more">Learn More</span>
    </article>
  </div>
</section>

<div class="why-img" role="img" aria-label="Open laptop computer"></div>
<section class="why">
  <h2 class="section-title">WHY CHOOSE US</h2>
  <ul>
    <li><svg viewBox="0 0 8 8"><path d="M1 4l2 2 4-5" fill="none" stroke="#0455a3" stroke-width="1.5"/></svg>Certified technicians with over ten years experience</li>
    <li><svg viewBox="0 0 8 8"><path d="M1 4l2 2 4-5" fill="none" stroke="#0455a3" stroke-width="1.5"/></svg>Fast turnaround on most repairs</li>
    <li><svg viewBox="0 0 8 8"><path d="M1 4l2 2 4-5" fill="none" stroke="#0455a3" stroke-width="1.5"/></svg>Clear upfront pricing with no hidden fees</li>
    <li><svg viewBox="0 0 8 8"><path d="M1 4l2 2 4-5" fill="none" stroke="#0455a3" stroke-width="1.5"/></svg>Friendly support for homes and offices</li>
    <li><svg viewBox="0 0 8 8"><path d="M1 4l2 2 4-5" fill="none" stroke="#0455a3" stroke-width="1.5"/></svg>Work guaranteed for ninety days</li>
  </ul>
  <span class="btn">Request Quote</span>
</section>

<footer class="footer">
  <nav class="footer-nav"><span>HOME</span><span>ABOUT US</span><span>SERVICES</span><span>WHY CHOOSE US</span><span>CONTACT</span></nav>
  <div class="copyright">© 2017 NEXBYTE. ALL RIGHTS RESERVED.</div>
  <div class="social"><span></span><span></span><span></span><span></span><span></span></div>
</footer>

</body>
</html>
```